RTavenor Business Cards & Letterhead

I have a logo but need a design for some new business cards. We are a Design-Build Firm that specializes in the design and construction of commercial projects.
the cards need to be professional. no cartoon stuff.
i would like to have the cards in AI format so I can update the card as needed. Logo is provided.
Our Address is: 4187 Marlowe Ct. Larkmoor, New Calder 27614

```html
<!DOCTYPE html>
<html lang="en">
<head>
<meta charset="UTF-8">
<title>RTavenor Business Card</title>
<link href="https://fonts.googleapis.com/css2?family=Montserrat:wght@400;500;700;800&display=swap" rel="stylesheet">
<style>
  :root {
    --backdrop: #3b3b3d;
    --card-white: #ffffff;
    --card-dark: #222222;
    --ink: #1f1f1f;
    --brand-blue: #1b75b8;
    --brand-blue-deep: #0f4f86;
    --text-light: #ffffff;
  }
  * { margin: 0; padding: 0; box-sizing: border-box; }
  html, body {
    width: 1200px;
    height: 1059px;
    overflow: hidden;
    background: var(--backdrop);
    font-family: "Montserrat", Arial, sans-serif;
  }
  .canvas { position: relative; width: 1200px; height: 1059px; }

  .card {
    position: absolute;
    border-radius: 18px;
    overflow: hidden;
    box-shadow: 0 8px 18px rgba(0,0,0,0.45);
  }
  .card-front { left: 256px; top: 100px; width: 688px; height: 391px; background: var(--card-white); }
  .card-back { left: 253px; top: 537px; width: 694px; height: 394px; background: var(--card-dark); }

  .brand {
    position: absolute;
    left: 0;
    right: 0;
    display: flex;
    align-items: center;
    justify-content: center;
  }
  .brand-square {
    background: linear-gradient(135deg, var(--brand-blue), var(--brand-blue-deep));
    border-radius: 3px;
  }
  .brand-name {
    font-weight: 800;
    letter-spacing: 0.5px;
    line-height: 1;
  }
  .card-front .brand { top: 94px; gap: 12px; }
  .card-front .brand-square { width: 48px; height: 48px; }
  .card-front .brand-name { font-size: 62px; color: var(--ink); }

  .card-back .brand { top: 174px; gap: 14px; }
  .card-back .brand-square { width: 57px; height: 57px; }
  .card-back .brand-name { font-size: 72px; color: var(--text-light); }

  .person {
    position: absolute;
    right: 377px;
    top: 215px;
    text-align: right;
  }
  .person-name {
    font-weight: 700;
    font-size: 26px;
    color: var(--brand-blue);
    letter-spacing: 1px;
    line-height: 1.1;
  }
  .person-role {
    font-weight: 400;
    font-size: 18px;
    color: var(--ink);
    letter-spacing: 1px;
    line-height: 1.2;
  }
  .divider {
    position: absolute;
    left: 343px;
    top: 210px;
    width: 2px;
    height: 64px;
    background: var(--brand-blue);
  }
  .contact-list {
    position: absolute;
    left: 372px;
    top: 205px;
    list-style: none;
  }
  .contact-item {
    display: flex;
    align-items: center;
    gap: 8px;
    height: 26px;
    font-size: 16.5px;
    color: var(--ink);
    letter-spacing: 0.4px;
  }
  .contact-icon { width: 13px; height: 13px; fill: var(--brand-blue); flex: none; }

  .address-band {
    position: absolute;
    left: 0;
    top: 324px;
    width: 100%;
    height: 26px;
    background: var(--card-dark);
    color: var(--text-light);
    font-size: 16px;
    letter-spacing: 0.4px;
    display: flex;
    align-items: center;
    justify-content: center;
  }
</style>
</head>
<body>
<main class="canvas">
  <section class="card card-front">
    <div class="brand">
      <span class="brand-square"></span>
      <span class="brand-name">RTAVENOR</span>
    </div>

    <div class="person">
      <p class="person-name">DANA WHITLOCK</p>
      <p class="person-role">MANAGER</p>
    </div>

    <div class="divider"></div>

    <ul class="contact-list">
      <li class="contact-item">
        <svg class="contact-icon" viewBox="0 0 24 24" aria-hidden="true"><path d="M6.6 10.8a15.1 15.1 0 0 0 6.6 6.6l2.2-2.2a1 1 0 0 1 1-.25 11.4 11.4 0 0 0 3.6.57 1 1 0 0 1 1 1V20a1 1 0 0 1-1 1A17 17 0 0 1 3 4a1 1 0 0 1 1-1h3.5a1 1 0 0 1 1 1c0 1.25.2 2.45.57 3.57a1 1 0 0 1-.25 1z"/></svg>
        123-456-7890
      </li>
      <li class="contact-item">
        <svg class="contact-icon" viewBox="0 0 24 24" aria-hidden="true"><path d="M2 5h20v14H2z"/><path d="M2 6.5l10 7 10-7V5H2z" fill="#fff"/></svg>
        info@youremail.com
      </li>
      <li class="contact-item">
        <svg class="contact-icon" viewBox="0 0 24 24" aria-hidden="true"><path d="M12 2a10 10 0 1 0 0 20 10 10 0 0 0 0-20zm6.9 6h-2.9a15.6 15.6 0 0 0-1.4-3.6A8 8 0 0 1 18.9 8zM12 4c.8 1.2 1.5 2.5 1.9 4h-3.8c.4-1.5 1.1-2.8 1.9-4zM4.3 14a8 8 0 0 1 0-4h3.4a16 16 0 0 0 0 4zm.8 2h2.9c.3 1.3.8 2.5 1.4 3.6A8 8 0 0 1 5.1 16zM8 8H5.1a8 8 0 0 1 4.3-3.6C8.8 5.5 8.3 6.7 8 8zm4 12c-.8-1.2-1.5-2.5-1.9-4h3.8c-.4 1.5-1.1 2.8-1.9 4zm2.3-6H9.7a14.7 14.7 0 0 1 0-4h4.6a14.7 14.7 0 0 1 0 4zm.3 5.6c.6-1.1 1.1-2.3 1.4-3.6h2.9a8 8 0 0 1-4.3 3.6zm1.7-5.6a16 16 0 0 0 0-4h3.4a8 8 0 0 1 0 4z"/></svg>
        www.yourwebsite.com
      </li>
    </ul>

    <div class="address-band">4187 Marlowe Ct. Larkmoor, New Calder 27614</div>
  </section>

  <section class="card card-back">
    <div class="brand">
      <span class="brand-square"></span>
      <span class="brand-name">RTAVENOR</span>
    </div>
  </section>
</main>
</body>
</html>
```